Corporate Travel Technology Company needs new Business Card design

We need a new business card design to reflect our re-branded company. Our company is called tolvEn (pronounced tolvenn) and we provide Business Intelligence and mobile travel management solutions for the corporate travel industry. Our multinational customers use our solutions to manage large travel budgets and frequent travellers, as well as to save money and reduce risk. We'd like to see designs that use the blue and green palette as well as our corporate logo (attached below). The design should communicate innovation, insight, forward thinking, contemporary, trusted.

Target Market(s)

Large multinational corporates and Travel Agencies.

Industry/Entity Type

Business

Contact Information for Business Card

Rosalind Mercer
Chief Executive
tolvEn
Phone number - +61 (0)2 8134 2907
Email address - rosalind.mercer@tolven-example.com
Mobile number - +61 (0)438 516 702
www.tolven-example.com

Font styles to use
Other font styles liked:
• Please use font as close to corporate logo as possible

Colors
0255a3
0393ce
00a990
33b8a4
33a6d7
3176b5

Requirements
Must have
• Please include the words;
• Mobile Travel Management
• Accelerating Travel Business Insights
• Use corporate logo - although icon can be stylised if needed

```html
<!DOCTYPE html>
<html lang="en">
<head>
<meta charset="utf-8">
<title>tolvEn business card</title>
<link rel="stylesheet" href="https://fonts.googleapis.com/css2?family=Open+Sans:wght@400;600;700&display=swap">
<style>
  :root {
    --page: #e9ecec;
    --card-white: #ffffff;
    --slate-dark: #1f2b2c;
    --slate-mid: #4a5a5b;
    --slate-light: #8d9d9b;
    --brand-blue: #33a6d7;
    --brand-blue-deep: #0393ce;
    --ink: #5d686c;
    --ink-soft: #3f4a4e;
    --on-dark: #ffffff;
  }
  * { box-sizing: border-box; margin: 0; padding: 0; }
  html, body {
    width: 1200px; height: 913px; overflow: hidden;
    background: var(--page);
    font-family: "Open Sans", Arial, sans-serif;
  }
  .sheet {
    width: 1200px; height: 913px;
    display: flex; align-items: center; justify-content: center; gap: 40px;
  }
  .card {
    position: relative; width: 540px; height: 330px;
    border-radius: 22px; overflow: hidden;
    box-shadow: 0 6px 18px rgba(0,0,0,0.18);
  }

  /* Front */
  .card--front { background: var(--card-white); }
  .card__band { position: absolute; inset: 0; width: 100%; height: 100%; }
  .contact {
    position: absolute; top: 38px; right: 34px; text-align: right;
  }
  .contact__name { font-size: 26px; font-weight: 700; color: var(--ink); line-height: 1.1; }
  .contact__title { font-size: 15px; color: var(--brand-blue); margin-bottom: 22px; }
  .contact__list { list-style: none; }
  .contact__item {
    display: flex; justify-content: flex-end; align-items: center; gap: 7px;
    font-size: 13.5px; color: var(--ink-soft); line-height: 1.6;
  }
  .contact__icon { width: 12px; height: 12px; flex: none; }
  .front-name {
    position: absolute; left: 40px; bottom: 52px;
    font-size: 64px; font-weight: 600; color: var(--brand-blue); letter-spacing: 1px;
  }

  /* Back */
  .card--back {
    background: linear-gradient(160deg, var(--slate-light) 0%, var(--slate-mid) 45%, var(--slate-dark) 100%);
    color: var(--on-dark);
  }
  .brand {
    position: absolute; left: 60px; top: 88px;
    display: flex; align-items: center; gap: 16px;
  }
  .brand__dot { width: 34px; height: 34px; border-radius: 50%; background: var(--brand-blue); }
  .brand__name { font-size: 84px; font-weight: 600; line-height: 1; color: var(--on-dark); }
  .taglines { position: absolute; left: 62px; top: 220px; list-style: none; }
  .taglines__item {
    display: flex; align-items: center; gap: 8px;
    font-size: 15px; line-height: 1.5; color: var(--on-dark);
  }
  .taglines__bullet { width: 9px; height: 9px; border-radius: 50%; border: 2px solid var(--brand-blue); }
</style>
</head>
<body>
<main class="sheet">
  <section class="card card--front" aria-label="Business card front">
    <svg class="card__band" viewBox="0 0 540 330" preserveAspectRatio="none" aria-hidden="true">
      <defs>
        <linearGradient id="slateFront" x1="0" y1="0" x2="0.4" y2="1">
          <stop offset="0" stop-color="#8d9d9b"/>
          <stop offset="0.5" stop-color="#4a5a5b"/>
          <stop offset="1" stop-color="#1f2b2c"/>
        </linearGradient>
      </defs>
      <path d="M0 120 C120 150 250 220 330 330 L0 330 Z" fill="url(#slateFront)"/>
    </svg>
    <span class="front-name">tolvEn</span>
    <div class="contact">
      <p class="contact__name">Rosalind Mercer</p>
      <p class="contact__title">Chief Executive</p>
      <ul class="contact__list">
        <li class="contact__item">+61 (0)438 516 702
          <svg class="contact__icon" viewBox="0 0 12 12" aria-hidden="true"><rect x="3" y="0.5" width="6" height="11" rx="1.2" fill="none" stroke="#33a6d7" stroke-width="1.2"/></svg></li>
        <li class="contact__item">+61 (0)2 8134 2907
          <svg class="contact__icon" viewBox="0 0 12 12" aria-hidden="true"><path d="M2 1.5 L4.5 1 L5.5 4 L4 5 C5 7 6 8 7.5 8.5 L8.5 7 L11 8 L10.5 10.5 C6 11 1 6 2 1.5Z" fill="none" stroke="#33a6d7" stroke-width="1.1"/></svg></li>
        <li class="contact__item">www.tolven-example.com
          <svg class="contact__icon" viewBox="0 0 12 12" aria-hidden="true"><circle cx="6" cy="6" r="5" fill="none" stroke="#33a6d7" stroke-width="1.1"/><path d="M1 6 H11 M6 1 C3.5 4 3.5 8 6 11 M6 1 C8.5 4 8.5 8 6 11" fill="none" stroke="#33a6d7" stroke-width="0.9"/></svg></li>
        <li class="contact__item">rosalind.mercer@tolven-example.com
          <svg class="contact__icon" viewBox="0 0 12 12" aria-hidden="true"><rect x="0.8" y="2.5" width="10.4" height="7" rx="1" fill="none" stroke="#33a6d7" stroke-width="1.1"/><path d="M1 3 L6 7 L11 3" fill="none" stroke="#33a6d7" stroke-width="1.1"/></svg></li>
      </ul>
    </div>
  </section>

  <section class="card card--back" aria-label="Business card back">
    <div class="brand">
      <span class="brand__dot"></span>
      <span class="brand__name">tolvEn</span>
    </div>
    <ul class="taglines">
      <li class="taglines__item"><span class="taglines__bullet"></span>Mobile Travel Management</li>
      <li class="taglines__item"><span class="taglines__bullet"></span>Accelerating Travel Business Insights</li>
    </ul>
  </section>
</main>
</body>
</html>
```